Free range pig farm business

We'd like a simple but elegant website for our new free range pig farm business.
Check out www.kelvorrahogsteads.com.au and http://www.tirrowfield.com.au/
pages:
Home
About
Shop
Contact
Target Market(s)
People who would want to find out where they could buy our pork
Industry/Entity Type
Agribusiness
Number of Pages Required
4 page
Font styles to use
Other font styles liked:
- As per our logo
Requirements
Must have
- Ability for us to update weekly with new news and photos

```html
<!DOCTYPE html>
<html lang="en">
<head>
<meta charset="utf-8">
<title>Coolabah Meadow Pork</title>
<link href="https://fonts.googleapis.com/css2?family=Open+Sans:wght@400;600;700;800&display=swap" rel="stylesheet">
<style>
:root{
  --paper:#f6f2ed;
  --white:#ffffff;
  --lime:#a9bf2c;
  --forest:#3a4f1d;
  --ink:#2e2e2e;
  --muted:#6b6b6b;
  --rule:#8a8a8a;
}
*{margin:0;padding:0;box-sizing:border-box}
html,body{width:710px;height:1200px;overflow:hidden}
body{position:relative;background:var(--paper);font-family:"Open Sans",sans-serif;color:var(--ink)}
.abs{position:absolute}

.follow{left:44px;top:22px;display:flex;align-items:center;gap:6px;font-size:7px;font-weight:700;color:var(--forest)}
.follow .label{margin-right:6px}
.follow .sq{width:13px;height:13px;background:#3b3b3b;border-radius:2px}

.brand{left:290px;top:10px;width:130px;text-align:center}
.brand .mark{width:30px;height:30px;border-radius:50%;background:var(--forest);margin:0 auto 6px}
.brand .name{font-size:9px;font-weight:600;color:var(--ink);line-height:1.35;letter-spacing:.2px}

.newsletter{left:463px;top:17px;display:flex;align-items:center}
.newsletter .label{font-size:7px;font-weight:700;color:var(--forest);margin-right:10px}
.newsletter .field{width:116px;height:24px;background:var(--white);border:1px solid #ddd;font-size:6.5px;color:#777;padding:7px 6px}
.newsletter .go{width:25px;height:24px;background:var(--lime);color:#fff;font-size:8px;font-weight:700;text-align:center;line-height:24px}

.nav{top:59px;height:29px;border-top:1px solid var(--rule);border-bottom:1px solid var(--rule);display:flex;align-items:center}
.nav a{font-size:10.5px;color:#444;text-decoration:none;letter-spacing:.3px}
.nav-left{left:44px;width:249px}
.nav-left .active{background:var(--lime);color:#fff;height:28px;line-height:28px;padding:0 15px;margin-left:21px}
.nav-left a+a{margin-left:22px}
.nav-right{left:417px;width:249px}
.nav-right a:first-child{margin-left:32px}
.nav-right a+a{margin-left:36px}
.nav-right svg{margin-left:50px}

.hero{left:44px;top:99px;width:622px;height:274px;background:radial-gradient(ellipse at 50% 45%,#c79a5e 0%,#a8773c 55%,#7a5426 100%)}
.hero h1{position:absolute;top:92px;width:100%;text-align:center;color:#fff;font-size:37px;font-weight:800;letter-spacing:1.5px}
.hero p{position:absolute;top:135px;width:100%;text-align:center;color:#fff;font-size:19px;font-weight:700}
.dots{position:absolute;top:249px;left:287px;display:flex;gap:6px}
.dots span{width:7px;height:7px;border-radius:50%;background:#fff}
.dots span:first-child{background:var(--lime)}

.welcome{left:44px;top:398px;width:622px;text-align:center}
.welcome h2{font-size:16.5px;font-weight:700;color:var(--forest);letter-spacing:.6px}
.welcome p{margin-top:10px;font-size:9.6px;line-height:17px;color:var(--muted);padding:0 10px}
.btn{display:inline-block;background:var(--lime);color:#fff;font-weight:700;text-align:center;letter-spacing:.4px}
.read-more{left:294px;top:518px;width:122px;height:26px;line-height:26px;font-size:9px}
.divider{left:44px;top:569px;width:622px;height:1px;background:#bbb}

.tile{top:596px;width:303px;height:163px;display:flex;align-items:center;justify-content:center;color:#fff;font-size:27px;font-weight:800;letter-spacing:1px}
.tile-pig{left:44px;background:linear-gradient(135deg,#3d5220,#24350f)}
.tile-pork{left:363px;background:linear-gradient(135deg,#2f4318,#6a5a3c)}

.shop{left:0;top:789px;width:710px;height:323px;background:var(--white)}
.shop h2{position:absolute;top:24px;width:100%;text-align:center;font-size:16px;font-weight:700;color:var(--forest);letter-spacing:.6px}
.product{position:absolute;top:63px;width:196px;text-align:center}
.product .photo{height:131px}
.product h3{margin-top:13px;font-size:8px;font-weight:700;color:#333;letter-spacing:.3px}
.product .desc{margin-top:2px;font-size:8px;color:var(--muted)}
.product .price{margin-top:5px;font-size:13px;font-weight:700;color:var(--forest)}
.product .btn{margin-top:10px;width:90px;height:26px;line-height:26px;font-size:8px}
.p1{left:44px}.p1 .photo{background:linear-gradient(135deg,#c8a684,#b4474f)}
.p2{left:257px}.p2 .photo{background:linear-gradient(135deg,#2a2a2a,#9a4652 60%,#c69a6a)}
.p3{left:469px}.p3 .photo{background:radial-gradient(ellipse at 50% 55%,#d69a86,#4a5a46 70%)}

.footer{left:0;top:1112px;width:710px;text-align:center}
.footer nav{margin-top:24px}
.footer nav a{font-size:7.5px;font-weight:700;color:#333;text-decoration:none;margin:0 10px;letter-spacing:.3px}
.footer p{font-size:6.8px;color:#444;line-height:13px}
.footer .copy{margin-top:8px}
</style>
</head>
<body>

<div class="abs follow">
  <span class="label">FOLLOW US</span>
  <span class="sq"></span><span class="sq"></span><span class="sq"></span><span class="sq"></span><span class="sq"></span>
</div>

<div class="abs brand">
  <div class="mark"></div>
  <div class="name">COOLABAH MEADOW<br>PORK</div>
</div>

<div class="abs newsletter">
  <span class="label">NEWSLETTER</span>
  <span class="field">Email Address</span>
  <span class="go">GO</span>
</div>

<nav class="abs nav nav-left">
  <a class="active" href="#">HOME</a><a href="#">ABOUT</a><a href="#">SERVICE</a>
</nav>
<nav class="abs nav nav-right">
  <a href="#">SHOP</a><a href="#">CONTACT US</a>
  <svg width="10" height="10" viewBox="0 0 10 10"><circle cx="4" cy="4" r="3" fill="none" stroke="#333" stroke-width="1.6"/><line x1="6.2" y1="6.2" x2="9.2" y2="9.2" stroke="#333" stroke-width="1.8"/></svg>
</nav>

<section class="abs hero" role="img" aria-label="Photo of young pigs standing on straw in a barn">
  <h1>PASTURED PORK</h1>
  <p>We are a new free range pig farm business.</p>
  <div class="dots"><span></span><span></span><span></span><span></span></div>
</section>

<section class="abs welcome">
  <h2>WELCOME TO COOLABAH MEADOW PORK</h2>
  <p>Aliquam molestie, mi et imperdiet euismod, dui purus auctor tellus, et interdum lacus lectus et ante. Sed accumsan sollicitudin sapien, sit amet adipiscing turpis gravida ac. In congue, neque ac lobortis volutpat, libero mauris varius mi, vitae suscipit ipsum ligula vitae risus. Duis aliquam nibh a dui iaculis viverra id a velit. Vivamus egestas risus in magna commodo. Sed semper viverra egestas. Etiam pretium porttitor lectus, vel ornare neque porta volutpat.</p>
</section>
<a class="abs btn read-more">READ MORE</a>
<div class="abs divider"></div>

<div class="abs tile tile-pig" role="img" aria-label="Photo of a pig in a grassy paddock under a dark green overlay">THE PIG</div>
<div class="abs tile tile-pork" role="img" aria-label="Photo of raw pork cuts with parsley under a dark green overlay">THE PORK</div>

<section class="abs shop">
  <h2>SHOP</h2>
  <div class="product p1">
    <div class="photo" role="img" aria-label="Photo of raw pork ribs with herbs and tomatoes"></div>
    <h3>NAM FERMENTUM</h3><p class="desc">Duis aliquam nibh a dui iaculis</p><p class="price">$40.00</p>
    <a class="btn">VIEW PRODUCT</a>
  </div>
  <div class="product p2">
    <div class="photo" role="img" aria-label="Photo of pork tenderloin on paper with spices"></div>
    <h3>NAM FERMENTUM</h3><p class="desc">Duis aliquam nibh a dui iaculis</p><p class="price">$40.00</p>
    <a class="btn">VIEW PRODUCT</a>
  </div>
  <div class="product p3">
    <div class="photo" role="img" aria-label="Photo of a pork roast on a wooden board"></div>
    <h3>NAM FERMENTUM</h3><p class="desc">Duis aliquam nibh a dui iaculis</p><p class="price">$40.00</p>
    <a class="btn">VIEW PRODUCT</a>
  </div>
</section>

<footer class="abs footer">
  <nav><a href="#">HOME</a><a href="#">ABOUT</a><a href="#">SERVICE</a><a href="#">SHOP</a><a href="#">CONTACT</a></nav>
  <p class="copy">Copyright © 2016. Company Name.</p>
  <p>All Right Reserved</p>
</footer>

</body>
</html>
```